Private Investment Firm Needs PowerPoint Presentation Template

Design PowerPoint template, take Pinebrook-submitted rough presentation draft, and drop it into new template. See attached Project Brief file for more detail.
Updates

Some decent designs have been submitted but they seem to lack the understanding of our target markets. I am hopeful that more time and feedback will result in better results.

Target Market(s)

Private company owners and intermediaries.

Font styles to use
Serif

Colors
3176b5

Requirements
Must have
• See attached Project Brief.
Nice to have
Should not have
• No B2C fluff--this is a B2B project.

```html
<!DOCTYPE html>
<html lang="en">
<head>
<meta charset="utf-8">
<title>Pinebrook – Introduction</title>
<link rel="stylesheet" href="https://fonts.googleapis.com/css2?family=Montserrat:wght@400;700&display=swap">
<style>
  :root {
    --brand-blue: #1a66ae;
    --ink: #3b3b3b;
    --ink-dark: #222222;
    --paper-top: #ececec;
    --paper-bottom: #ffffff;
  }
  * { margin: 0; padding: 0; box-sizing: border-box; }
  html, body { width: 1200px; height: 770px; overflow: hidden; background: #ffffff; }
  .slide {
    position: relative; width: 1200px; height: 770px; overflow: hidden;
    background: linear-gradient(160deg, var(--paper-top) 0%, #f7f7f7 45%, var(--paper-bottom) 100%);
    font-family: "Montserrat", Arial, sans-serif; color: var(--ink);
  }
  .corner { position: absolute; display: block; }
  .corner--top-left { left: 0; top: 0; }
  .corner--bottom-right { right: 0; bottom: 0; }

  .slide-title {
    position: absolute; left: 0; right: 0; top: 52px; text-align: center;
    font-weight: 700; font-size: 44px; letter-spacing: 1px; line-height: 58px;
    color: var(--brand-blue);
  }
  .title-rule {
    position: absolute; left: 570px; top: 112px; width: 60px; height: 6px;
    border-radius: 3px; background: var(--brand-blue);
  }

  .line, .para {
    position: absolute; left: 210px; font-size: 18.5px; letter-spacing: 0.3px;
    white-space: nowrap;
  }
  .line { line-height: 30px; }
  .para { white-space: normal; line-height: 22px; text-align: justify; }
  .para--narrow { width: 752px; }
  .para--wide { width: 796px; }
  .dot {
    position: absolute; left: 184px; width: 9px; height: 9px; border-radius: 50%;
    background: var(--brand-blue);
  }
  .option { left: 212px; display: flex; align-items: center; gap: 4px; }
  .option svg { flex: none; margin-top: 6px; }

  .brand {
    position: absolute; left: 0; right: 0; top: 568px;
    display: flex; justify-content: center; align-items: center; gap: 10px;
  }
  .brand-mark { width: 12px; height: 12px; background: var(--brand-blue); }
  .brand-name { font-size: 20px; letter-spacing: 2px; color: var(--brand-blue); line-height: 24px; }
  .web {
    position: absolute; left: 0; right: 0; top: 618px; text-align: center;
    font-size: 19px; line-height: 24px; color: var(--ink-dark);
  }
  .web strong { color: var(--brand-blue); font-weight: 700; }
  .page-number {
    position: absolute; left: 1142px; top: 627px;
    font-size: 11px; font-weight: 700; color: #ffffff;
  }
</style>
</head>
<body>
<main class="slide">
  <svg class="corner corner--top-left" width="150" height="169" viewBox="0 0 150 169" aria-hidden="true">
    <polygon points="0,0 150,0 0,169" fill="#1660a6"/>
  </svg>
  <svg class="corner corner--bottom-right" width="334" height="470" viewBox="0 0 334 470" aria-hidden="true">
    <defs>
      <linearGradient id="cornerFade" x1="0" y1="1" x2="1" y2="0">
        <stop offset="0" stop-color="#3592d2"/>
        <stop offset="1" stop-color="#1e6fb4"/>
      </linearGradient>
    </defs>
    <polygon points="334,0 334,470 0,470" fill="url(#cornerFade)"/>
  </svg>

  <h1 class="slide-title">INTRODUCTION</h1>
  <div class="title-rule"></div>

  <span class="dot" style="top:159px"></span>
  <p class="line" style="top:150px">Private company owners have traditionally considered two capital raising options</p>
  <p class="line option" style="top:180px">
    <svg width="16" height="14" viewBox="0 0 16 14" aria-hidden="true"><path d="M2 8 L6 12 L14 2" fill="none" stroke="#1a66ae" stroke-width="2"/></svg>
    Borrow from a local bank, or
  </p>
  <p class="line option" style="top:210px">
    <svg width="16" height="14" viewBox="0 0 16 14" aria-hidden="true"><path d="M2 8 L6 12 L14 2" fill="none" stroke="#1a66ae" stroke-width="2"/></svg>
    Sell most or all of the company to a change- of-control investor (aka Buyout firm)
  </p>

  <span class="dot" style="top:277px"></span>
  <p class="para para--narrow" style="top:273px">An alternative most have not considered is the raising of Non-Control Capital, or capital that is invested into the business yet allows those same owners to retain controlling interest in their company</p>

  <span class="dot" style="top:381px"></span>
  <p class="para para--narrow" style="top:377px">Non-Control Capital is not appropriate for every private company owner but neither is a Change-of-Control sale</p>

  <span class="dot" style="top:464px"></span>
  <p class="para para--wide" style="top:460px">The key is to determine what the business and owners require, and then partner with an investor best aligned with those needs so that long-term company growth, and personal goals, can both be achieved</p>

  <div class="brand">
    <span class="brand-mark"></span>
    <span class="brand-name">PINEBROOK</span>
  </div>
  <div class="web">www.<strong>pinebrookquillfield</strong>.com</div>
  <div class="page-number">1.</div>
</main>
</body>
</html>
```